KRV Business Card

Looking for a business card for my restaurant group I own. Four different concepts:

Copperfield Alehouse
Bristow Alehouse
Tanager's Stone Hearth Kitchen
Pellston Patty Company

Card doesn't need to include all the logos.

```html
<!DOCTYPE html>
<html lang="en">
<head>
<meta charset="UTF-8">
<title>KRV Business Card</title>
<link href="https://fonts.googleapis.com/css2?family=Poppins:ital,wght@0,400;0,600;1,400&display=swap" rel="stylesheet">
<style>
  :root {
    --gold: #cfad6c;
    --slate: #6e6f73;
    --white: #ffffff;
    --stage: #ebe7e1;
    --ink-soft: #6b6c70;
  }
  * { margin: 0; padding: 0; box-sizing: border-box; }
  html, body {
    width: 1125px; height: 1200px; overflow: hidden;
    background: var(--stage);
    font-family: "Poppins", sans-serif;
  }
  .canvas { position: relative; width: 1125px; height: 1200px; }
  .card {
    position: absolute; left: 171px; width: 826px; height: 470px;
    box-shadow: 0 6px 16px rgba(0,0,0,0.18);
  }
  .card--front { top: 106px; background: var(--white); display: flex; }
  .card--back { top: 639px; background: var(--slate); }

  .brand-side {
    width: 446px; height: 100%;
    display: flex; flex-direction: column; align-items: center; justify-content: center;
  }
  .brand-name {
    color: var(--gold); font-weight: 600; font-size: 34px;
    letter-spacing: 2px; text-transform: uppercase; text-align: center; line-height: 1.25;
  }
  .brand-name span { display: block; }
  .brand-mark {
    width: 18px; height: 18px; background: var(--gold); margin-bottom: 22px;
  }

  .info-side { width: 380px; height: 100%; display: flex; flex-direction: column; gap: 4px; }
  .panel { color: var(--white); padding-left: 39px; display: flex; flex-direction: column; justify-content: center; }
  .panel--identity { background: var(--gold); height: 149px; }
  .panel--phones { background: var(--slate); height: 153px; font-size: 19px; line-height: 1.4; }
  .panel--address { background: var(--gold); flex: 1; font-size: 19px; line-height: 1.4; }
  .person-name { font-weight: 600; font-size: 30px; line-height: 1.15; }
  .person-title { font-size: 21px; line-height: 1.2; }
  .person-email { font-style: italic; font-size: 19px; line-height: 1.35; }

  .back-mark {
    position: absolute; top: 110px; left: 0; width: 100%;
    text-align: center; color: var(--white);
    font-weight: 600; font-size: 170px; line-height: 1; letter-spacing: 6px;
  }
  .back-url {
    position: absolute; top: 392px; left: 0; width: 100%;
    text-align: center; color: var(--white);
    font-size: 19px; letter-spacing: 4px;
  }
</style>
</head>
<body>
<main class="canvas">
  <section class="card card--front">
    <div class="brand-side">
      <div class="brand-mark"></div>
      <p class="brand-name"><span>Kestrel Ridge</span><span>Ventures</span></p>
    </div>
    <div class="info-side">
      <div class="panel panel--identity">
        <p class="person-name">Daniel Hayes</p>
        <p class="person-title">President</p>
        <p class="person-email">info@kestrelridgeventures.com</p>
      </div>
      <div class="panel panel--phones">
        <p>Tel: 555-214-7390</p>
        <p>Fax: 555-418-2263</p>
        <p>Mob: 555-307-6841</p>
      </div>
      <div class="panel panel--address">
        <p>2140 Alder Court</p>
        <p>Juneau, Alaska 99801</p>
        <p>www.kestrelridgeventures.com</p>
      </div>
    </div>
  </section>

  <section class="card card--back">
    <p class="back-mark">KRV</p>
    <p class="back-url">WWW.KESTRELRIDGEVENTURES.COM</p>
  </section>
</main>
</body>
</html>
```